sydney wedding photography business needs a business card design

we need a business card design for a sydney based wedding photography and videography business. our business name is :golden hour studio and film. our target clients are 24-35 yrs female. our style is candid, organic, natural, dynamic. we are a team of young photographers and videographers, and help brides to create memories that they will cherish for the rest of their lives. the logo will be provided. we want an elegant design that reflects our style, and also want to give a great impression to our clients that we are one of the best studios in sydney and our brand means quality and premium service.

Target Market(s)

bride to be, 24-35 years old, living in sydney and surrunding areas

Industry/Entity Type

Wedding Photography

Contact Information for Business Card

address: 57 tarrant street, glenmore nsw 2047
mobile: 0431872259
phone: (02) 9163 2408
info@tidewillowstudio.net.au
www.tidewillowstudio.net.au
facebook:tidewillowweddings
instagram:tidewillowweddings

Font styles to use
Serif
Sans Serif

Requirements
Nice to have
• maybe add my slogan"memories beyond eternity" if the layout looks good
Should not have
• no black color, not good idea for wedding biz card

```html
<!DOCTYPE html>
<html lang="en">
<head>
<meta charset="utf-8">
<title>Golden Hour Studio and Film – Business Card</title>
<link href="https://fonts.googleapis.com/css2?family=Jost:wght@400;500&display=swap" rel="stylesheet">
<style>
  :root {
    --page-bg: #e9e6e0;
    --gold-light: #f0c23a;
    --gold-mid: #d9a21c;
    --gold-deep: #a87410;
    --ink: #1a1408;
    --icon-fill: #e2b030;
    --card-back-top: #4a3318;
    --card-back-bottom: #2f200e;
    --foil: #e6b436;
  }
  html, body {
    margin: 0;
    padding: 0;
    width: 1200px;
    height: 950px;
    overflow: hidden;
    background: var(--page-bg);
    font-family: "Jost", "Futura", sans-serif;
  }
  .canvas {
    position: relative;
    width: 1200px;
    height: 950px;
  }
  .card {
    position: absolute;
    top: 197px;
    width: 340px;
    height: 556px;
    box-shadow: 0 14px 30px rgba(0,0,0,0.25);
  }
  .card-front {
    left: 170px;
    background: linear-gradient(150deg, var(--gold-mid) 0%, var(--gold-light) 45%, var(--gold-deep) 100%);
    color: var(--ink);
  }
  .card-back {
    left: 690px;
    background: linear-gradient(160deg, var(--card-back-top) 0%, var(--card-back-bottom) 100%);
  }
  .card-frame {
    position: absolute;
    inset: 14px;
    border: 1px solid var(--ink);
  }
  .card-back .card-frame { border-color: var(--foil); }
  .corner-flourish {
    position: absolute;
    width: 34px;
    height: 34px;
  }
  .corner-flourish.tl { top: 8px; left: 8px; }
  .corner-flourish.tr { top: 8px; right: 8px; }
  .corner-flourish.bl { bottom: 8px; left: 8px; }
  .corner-flourish.br { bottom: 8px; right: 8px; }

  .identity {
    position: absolute;
    top: 52px;
    left: 0;
    right: 0;
    text-align: center;
  }
  .identity .badge { display: block; margin: 0 auto 6px; }
  .person-name {
    font-size: 25px;
    font-weight: 500;
    letter-spacing: 2px;
    line-height: 1;
    margin: 0;
  }
  .person-role {
    font-size: 12px;
    letter-spacing: 2.5px;
    margin: 3px 0 0;
  }
  .contact-list {
    position: absolute;
    top: 175px;
    right: 36px;
    margin: 0;
    padding: 0;
    list-style: none;
  }
  .contact-item {
    display: flex;
    justify-content: flex-end;
    align-items: center;
    gap: 10px;
    height: 41px;
    font-size: 15px;
    letter-spacing: 0.3px;
    white-space: nowrap;
    font-variant-ligatures: none;
  }
  .contact-item.address { font-size: 13.5px; }
  .icon { flex: none; }

  .brand {
    position: absolute;
    inset: 0;
    display: flex;
    flex-direction: column;
    justify-content: center;
    align-items: center;
    color: var(--foil);
    font-weight: 500;
    text-align: center;
  }
  .brand-main {
    font-size: 46px;
    line-height: 1;
    letter-spacing: 1px;
  }
  .brand-sub {
    font-size: 14px;
    letter-spacing: 6px;
    margin-top: 12px;
    text-transform: uppercase;
  }
</style>
</head>
<body>
<main class="canvas">

  <section class="card card-front" aria-label="Business card front">
    <div class="card-frame"></div>
    <svg class="corner-flourish tl" role="img" aria-label="Corner flourish ornament"><rect width="34" height="34" fill="#b8841a" opacity="0.45"/></svg>
    <svg class="corner-flourish tr" role="img" aria-label="Corner flourish ornament"><rect width="34" height="34" fill="#b8841a" opacity="0.45"/></svg>
    <svg class="corner-flourish bl" role="img" aria-label="Corner flourish ornament"><rect width="34" height="34" fill="#b8841a" opacity="0.45"/></svg>
    <svg class="corner-flourish br" role="img" aria-label="Corner flourish ornament"><rect width="34" height="34" fill="#b8841a" opacity="0.45"/></svg>

    <header class="identity">
      <svg class="badge" width="24" height="24" viewBox="0 0 24 24" aria-hidden="true">
        <circle cx="12" cy="12" r="12" fill="#1a1408"/>
        <circle cx="12" cy="9.5" r="3.6" fill="#e2b030"/>
        <path d="M5.5 19c1-3.6 3.6-5 6.5-5s5.5 1.4 6.5 5z" fill="#e2b030"/>
      </svg>
      <h1 class="person-name">MARCUS HALE</h1>
      <p class="person-role">PHOTOGRAPHER</p>
    </header>

    <ul class="contact-list">
      <li class="contact-item">(02) 9163 2408
        <svg class="icon" width="22" height="22" viewBox="0 0 22 22" aria-hidden="true"><circle cx="11" cy="11" r="11" fill="#1a1408"/><path d="M7.5 5.5l2 2.2-1 1.4c.8 1.7 2 2.9 3.6 3.6l1.4-1 2.2 2-1 1.8c-3.8-.3-7.6-4.1-7.9-7.9z" fill="#e2b030"/></svg>
      </li>
      <li class="contact-item">(04) 3187 2259
        <svg class="icon" width="22" height="22" viewBox="0 0 22 22" aria-hidden="true"><circle cx="11" cy="11" r="11" fill="#1a1408"/><rect x="7.5" y="5" width="7" height="12" rx="1.2" fill="none" stroke="#e2b030" stroke-width="1.4"/><circle cx="11" cy="15" r="0.8" fill="#e2b030"/></svg>
      </li>
      <li class="contact-item">info@tidewillowstudio.net.au
        <svg class="icon" width="22" height="22" viewBox="0 0 22 22" aria-hidden="true"><circle cx="11" cy="11" r="11" fill="#1a1408"/><rect x="5.5" y="7" width="11" height="8" fill="none" stroke="#e2b030" stroke-width="1.3"/><path d="M5.5 7l5.5 4.5L16.5 7" fill="none" stroke="#e2b030" stroke-width="1.3"/></svg>
      </li>
      <li class="contact-item">www.tidewillowstudio.net.au
        <svg class="icon" width="22" height="22" viewBox="0 0 22 22" aria-hidden="true"><circle cx="11" cy="11" r="11" fill="#1a1408"/><circle cx="11" cy="11" r="5.5" fill="none" stroke="#e2b030" stroke-width="1.2"/><ellipse cx="11" cy="11" rx="2.4" ry="5.5" fill="none" stroke="#e2b030" stroke-width="1.1"/><path d="M5.5 11h11" stroke="#e2b030" stroke-width="1.1"/></svg>
      </li>
      <li class="contact-item">tidewillowstudio.net.au
        <svg class="icon" width="22" height="22" viewBox="0 0 22 22" aria-hidden="true"><circle cx="11" cy="11" r="11" fill="#1a1408"/><path d="M9.8 12.2l2.4-2.4" stroke="#e2b030" stroke-width="1.4" stroke-linecap="round"/><path d="M10.6 8.4l1.2-1.2a2.3 2.3 0 0 1 3.2 3.2l-1.2 1.2" fill="none" stroke="#e2b030" stroke-width="1.4" stroke-linecap="round"/><path d="M11.4 13.6l-1.2 1.2a2.3 2.3 0 0 1-3.2-3.2l1.2-1.2" fill="none" stroke="#e2b030" stroke-width="1.4" stroke-linecap="round"/></svg>
      </li>
      <li class="contact-item">tidewillowweddings
        <svg class="icon" width="22" height="22" viewBox="0 0 22 22" aria-hidden="true"><circle cx="11" cy="11" r="11" fill="#1a1408"/><path d="M5.5 8.5h2.6l1-1.6h3.8l1 1.6h2.6v7h-11z" fill="#e2b030"/><circle cx="11" cy="11.8" r="2.1" fill="#1a1408"/></svg>
      </li>
      <li class="contact-item address">57 tarrant street, glenmore nsw 2047
        <svg class="icon" width="22" height="22" viewBox="0 0 22 22" aria-hidden="true"><circle cx="11" cy="11" r="11" fill="#1a1408"/><path d="M11 17s-4-4.3-4-7.2a4 4 0 0 1 8 0C15 12.7 11 17 11 17z" fill="#e2b030"/><circle cx="11" cy="9.8" r="1.5" fill="#1a1408"/></svg>
      </li>
    </ul>
  </section>

  <section class="card card-back" aria-label="Business card back">
    <div class="card-frame"></div>
    <svg class="corner-flourish tl" role="img" aria-label="Corner flourish ornament"><rect width="34" height="34" fill="#e6b436" opacity="0.3"/></svg>
    <svg class="corner-flourish tr" role="img" aria-label="Corner flourish ornament"><rect width="34" height="34" fill="#e6b436" opacity="0.3"/></svg>
    <svg class="corner-flourish bl" role="img" aria-label="Corner flourish ornament"><rect width="34" height="34" fill="#e6b436" opacity="0.3"/></svg>
    <svg class="corner-flourish br" role="img" aria-label="Corner flourish ornament"><rect width="34" height="34" fill="#e6b436" opacity="0.3"/></svg>
    <div class="brand">
      <span class="brand-main">golden hour</span>
      <span class="brand-sub">studio and film</span>
    </div>
  </section>

</main>
</body>
</html>
```